Veltrane Group Business Card Design

The CEO is looking for a new trendy look for his business card.
You can stay with current branding or come up with something new/creative. It can be 3D, including Medical Office buildings. You can use our logo in a variety of colors. Please include name, title, company name, company website, email address, cell number

Target Market(s)

Real Estate Development and Construction

Industry/Entity Type

Health care real estate

Contact Information for Business Card

Rohesh Kamdar, CEO M-604.781.2249 E-roheshkamdar@veltrane.com Address:4180 Lindqvist Ave, Tampa, FL 33482 www.veltrane.com

Font styles to use
Other font styles liked:
• Be creative

Requirements
Must have
• Creative, trendy look
Nice to have
• Please go to our website to get a feel- www. veltrane.com
Should not have
• small fonts

```html
<!DOCTYPE html>
<html lang="en">
<head>
<meta charset="utf-8">
<title>Veltrane Group Business Card</title>
<link rel="stylesheet" href="https://fonts.googleapis.com/css2?family=Montserrat:wght@400;700;900&display=swap">
<style>
  :root {
    --stage: #3a3a3a;
    --card-dark: #0e0e0e;
    --mark-dark: #1d1d1d;
    --card-light: #ffffff;
    --ink: #111111;
    --ink-soft: #2a2a2a;
  }
  * { box-sizing: border-box; margin: 0; padding: 0; }
  html, body { width: 1200px; height: 875px; overflow: hidden; }
  body {
    background: var(--stage);
    font-family: "Montserrat", sans-serif;
    position: relative;
  }
  .card {
    position: absolute;
    left: 300px;
    width: 600px;
    height: 340px;
    border-radius: 22px;
  }
  .card--back {
    top: 95px;
    background: var(--card-dark);
    display: flex;
    align-items: center;
    justify-content: center;
  }
  .card--front {
    top: 465px;
    background: var(--card-light);
    display: flex;
    align-items: center;
    padding: 0 40px 0 50px;
  }
  .wordmark {
    font-weight: 900;
    letter-spacing: -1px;
    line-height: 1;
  }
  .card--back .wordmark { color: var(--mark-dark); font-size: 62px; }
  .card--front .wordmark { color: var(--ink); font-size: 38px; }
  .divider {
    width: 2px;
    height: 180px;
    background: var(--ink);
    margin: 0 22px 0 26px;
  }
  .details { color: var(--ink-soft); font-size: 14px; line-height: 1.35; }
  .details__name { font-weight: 700; font-size: 22px; color: var(--ink); }
  .details__title { margin-bottom: 12px; }
  .details__address { margin-bottom: 10px; }
  .contact-line { display: flex; align-items: center; gap: 8px; margin-top: 4px; }
  .contact-line svg { width: 13px; height: 13px; flex: none; }
</style>
</head>
<body>
  <section class="card card--back">
    <span class="wordmark">Veltrane Group</span>
  </section>

  <section class="card card--front">
    <span class="wordmark">Veltrane Group</span>
    <div class="divider"></div>
    <div class="details">
      <p class="details__name">Rohesh Kamdar</p>
      <p class="details__title">CEO</p>
      <p class="details__address">4180 Lindqvist Ave,<br>Tampa, FL 33482</p>
      <p class="contact-line">
        <svg viewBox="0 0 16 16" aria-hidden="true"><path fill="#111" d="M3.6 1.5 6 4 4.8 5.6c.8 1.8 2.2 3.2 4 4l1.6-1.2 2.5 2.4-1.5 2.2C6.7 13 2.9 9.2 1.5 3.1z"/></svg>
        604.781.2249
      </p>
      <p class="contact-line">
        <svg viewBox="0 0 16 16" aria-hidden="true"><rect x="1" y="3" width="14" height="10" rx="1" fill="#111"/><path d="M1.5 3.5 8 9l6.5-5.5" stroke="#fff" stroke-width="1.2" fill="none"/></svg>
        roheshkamdar@veltrane.com
      </p>
      <p class="contact-line">
        <svg viewBox="0 0 16 16" aria-hidden="true"><circle cx="8" cy="8" r="6.5" fill="none" stroke="#111" stroke-width="1.5"/><ellipse cx="8" cy="8" rx="2.6" ry="6.5" fill="none" stroke="#111" stroke-width="1.2"/><path d="M1.5 8h13" stroke="#111" stroke-width="1.2"/></svg>
        www.veltrane.com
      </p>
    </div>
  </section>
</body>
</html>
```